Business card design for a dynamic IT consulting company

We need a business card design for a young firm, specialized in the Telecommunications/Consulting industry. The name of the company is Quindor and Partners Business Consulting Ltd. (Short name: Quindor and Partnes)
Quindor = solve read reverse, so we aim to be uncomplicated and solution-oriented. The small pipe in our logo is also related to the word solve. So we need a new business card design, which is simple, eye catching and something non traditional (I would probably prefer a square shaped design rather than a rectangle, but open for suggestions). Attached our logo.

Target Market(s)

Usually our customers are Tier1 Telecoms providers (Q-Netra, Palorix, etc) and their executives.

Industry/Entity Type

Business

Contact Information for Business Card

Name: Bence Tolnavari
Email: b.tolnavari@quindor.hu
Web: www.quindor.hu
Mobile: +36 30 518 2769
Title: Managing Director

Optional:
Company name: Quindor and Partners Ltd.
Address: 1087 Budapest, Tolvenka str. 28/C, Hungary

Font styles to use
Other font styles liked:
• helveticaneue_medium, Prime Regular are used now.

Colors

Designer to choose colors to be used in the design.

Requirements
Must have
• I would like to have a 2 sided design.
Nice to have
• I thought if we make the logo a bit bigger (without the company name), that could go to the back with the company name below. I though, if the pipe in the logo is somehow touchable on the business card, would be nice and unique.

```html
<!DOCTYPE html>
<html lang="en">
<head>
<meta charset="utf-8">
<title>Quindor and Partners – Business Card</title>
<link href="https://fonts.googleapis.com/css2?family=Exo+2:wght@500&family=Work+Sans:wght@400&display=swap" rel="stylesheet">
<style>
  :root {
    --backdrop: #161616;
    --card: #232323;
    --card-edge: #2c2c2c;
    --white: #f2f2f2;
    --muted: #d9d9d9;
    --blue: #1e9ee0;
    --magenta: #c1269a;
  }
  * { margin: 0; padding: 0; box-sizing: border-box; }
  html, body { width: 1200px; height: 900px; overflow: hidden; }
  body {
    background: var(--backdrop);
    display: flex;
    flex-direction: column;
    align-items: center;
    justify-content: center;
    gap: 40px;
    font-family: "Work Sans", sans-serif;
    color: var(--white);
  }
  .card {
    width: 700px;
    height: 390px;
    background: linear-gradient(135deg, var(--card) 0%, var(--card-edge) 100%);
    position: relative;
    box-shadow: 0 10px 30px rgba(0,0,0,.5);
  }

  /* Company name placeholder: body font, one colour, one weight */
  .company-mark {
    font-family: "Work Sans", sans-serif;
    font-weight: 400;
    color: var(--white);
    white-space: nowrap;
    display: flex;
    align-items: center;
    gap: 0.45em;
  }
  .company-mark-square {
    display: inline-block;
    width: 0.45em;
    height: 0.45em;
    background: var(--white);
  }

  /* Front */
  .card-front .company-mark {
    position: absolute;
    top: 140px;
    left: 0; right: 0;
    justify-content: center;
    font-size: 42px;
  }
  .card-front .website {
    position: absolute;
    bottom: 70px;
    left: 0; right: 0;
    text-align: center;
    font-size: 16px;
    letter-spacing: 3px;
  }

  /* Back */
  .card-back .company-mark {
    position: absolute;
    top: 190px;
    left: 42px;
    font-size: 24px;
  }
  .divider {
    position: absolute;
    left: 340px;
    top: 110px;
    width: 2px;
    height: 200px;
    background: var(--magenta);
  }
  .contact {
    position: absolute;
    left: 370px;
    top: 108px;
  }
  .person-name {
    font-family: "Exo 2", sans-serif;
    font-weight: 500;
    font-size: 24px;
    color: var(--blue);
    letter-spacing: 1px;
    text-transform: uppercase;
  }
  .person-title { font-size: 15px; color: var(--muted); margin-bottom: 10px; }
  .company-name {
    font-family: "Exo 2", sans-serif;
    font-weight: 500;
    font-size: 15px;
    color: var(--blue);
    text-transform: uppercase;
  }
  .address { font-size: 14px; line-height: 1.35; margin-bottom: 10px; }
  .contact-list { list-style: none; font-size: 14px; line-height: 1.65; }
  .contact-list li { display: flex; align-items: center; gap: 10px; }
  .contact-list svg { width: 13px; height: 13px; fill: none; stroke: var(--blue); stroke-width: 2; }
</style>
</head>
<body>

  <section class="card card-front" aria-label="Card front">
    <div class="company-mark"><span class="company-mark-square"></span>Quindor and Partners</div>
    <p class="website">www.quindor.hu</p>
  </section>

  <section class="card card-back" aria-label="Card back">
    <div class="company-mark"><span class="company-mark-square"></span>Quindor and Partners</div>
    <div class="divider"></div>
    <div class="contact">
      <h1 class="person-name">Bence Tolnavari</h1>
      <p class="person-title">Managing Director</p>
      <p class="company-name">Quindor and Partners Ltd.</p>
      <p class="address">1087 Budapest, Tolvenka<br>str. 28/C, Hungary</p>
      <ul class="contact-list">
        <li>
          <svg viewBox="0 0 24 24" aria-hidden="true"><path d="M5 3h4l2 5-3 2a12 12 0 0 0 6 6l2-3 5 2v4a2 2 0 0 1-2 2A17 17 0 0 1 3 5a2 2 0 0 1 2-2z"/></svg>
          +36 30 518 2769
        </li>
        <li>
          <svg viewBox="0 0 24 24" aria-hidden="true"><rect x="2" y="5" width="20" height="14"/><path d="M2 5l10 8 10-8"/></svg>
          b.tolnavari@quindor.hu
        </li>
        <li>
          <svg viewBox="0 0 24 24" aria-hidden="true"><circle cx="12" cy="12" r="10"/><path d="M2 12h20M12 2c3 3 3 17 0 20M12 2c-3 3-3 17 0 20"/></svg>
          www.quindor.hu
        </li>
      </ul>
    </div>
  </section>

</body>
</html>
```